Easy Marinade Labels for Butchery Store

Need a set of labels designed for a Butchery Shop. They will sit in the top left corner of the packets as a triangle (7cm each side). Easy because the only major requirement is the label name and some small text saying "Please ask in store to see spec sheet for ingredients". Extra points for finding a fun way to incorporate the logo and/or images of food (garlic bulbs, chilli, spices ect) to enhance the label. List of Marinade Names below: GarlicPepper Mint & RosemarySatayBBQChilli Plum & GingerSundried Tomato & BasilBuffaloHoney SoyHoi-SinPer PeriSpicy CajunTeriyakiBlack Bean Ive also attached the logo and an example of how the label might sit on a packet of meat. Thanks

Target Market(s)

Butchery Deli Shop Customers

Industry/Entity Type

Food Store

Font styles to use
Serif
Sans Serif
Decorative
Other font styles liked:
• Fun font that isn't a generic Quellbrix Font?

Colors

Designer to choose colors to be used in the design.

Requirements
Must have
• Product Name
• Small text saying "Please ask in store to see spec sheet for ingredients"
Nice to have
• Photos of ingredients that would match that type of marinade - Chilli, Garlic, Spices.
• Fenly Oak Logo - not essential if it doesn't look good on the label / doesn't fit.

```html
<!DOCTYPE html>
<html lang="en">
<head>
<meta charset="utf-8">
<title>Marinade Label – Mint and Rosemary</title>
<link rel="stylesheet" href="https://fonts.googleapis.com/css2?family=Amatic+SC:wght@700&family=Montserrat:wght@700;800&family=Pacifico&display=swap">
<style>
  :root {
    --paper: #ffffff;
    --frame-yellow: #e9e524;
    --herb-light: #8fcf3a;
    --herb-mid: #3f9a2c;
    --herb-deep: #1f6a1e;
    --herb-dark: #114d16;
    --label-text: #ffffff;
    --text-shadow: #0d3310;
  }
  html, body {
    margin: 0;
    padding: 0;
    width: 1200px;
    height: 900px;
    overflow: hidden;
    background: var(--paper);
  }
  .label-canvas {
    display: block;
    width: 1200px;
    height: 900px;
  }
  .label-frame { fill: var(--frame-yellow); }
  .kicker {
    font-family: "Montserrat", sans-serif;
    font-weight: 700;
    font-size: 14px;
    letter-spacing: 2.5px;
    fill: var(--label-text);
  }
  .product-name {
    font-family: "Amatic SC", cursive;
    font-weight: 700;
    fill: var(--label-text);
    stroke: var(--text-shadow);
    stroke-width: 1.2px;
    paint-order: stroke;
  }
  .product-name--first { font-size: 78px; letter-spacing: 2px; }
  .product-name--second { font-size: 74px; letter-spacing: 2px; }
  .connector {
    font-family: "Pacifico", cursive;
    font-size: 26px;
    fill: var(--label-text);
  }
  .connector-swash {
    fill: none;
    stroke: var(--label-text);
    stroke-width: 4;
    stroke-linecap: round;
  }
  .ingredients-note {
    font-family: "Montserrat", sans-serif;
    font-weight: 800;
    font-size: 18.5px;
    letter-spacing: 1.6px;
    fill: var(--label-text);
    stroke: var(--text-shadow);
    stroke-width: 2px;
    paint-order: stroke;
  }
</style>
</head>
<body>
<svg class="label-canvas" viewBox="0 0 1200 900" xmlns="http://www.w3.org/2000/svg">
  <defs>
    <linearGradient id="herbTone" x1="0" y1="0" x2="1" y2="1">
      <stop offset="0" stop-color="var(--herb-light)"/>
      <stop offset="0.45" stop-color="var(--herb-mid)"/>
      <stop offset="0.8" stop-color="var(--herb-deep)"/>
      <stop offset="1" stop-color="var(--herb-dark)"/>
    </linearGradient>
  </defs>

  <polygon class="label-frame" points="620,169 1100,649 140,649"/>
  <polygon class="herb-backdrop" role="img"
           aria-label="Watercolour illustration of fresh mint leaves and rosemary sprigs"
           fill="url(#herbTone)" points="620,182 1084,642 156,642"/>

  <text class="kicker" x="615" y="368" text-anchor="middle">MARINATED WITH</text>

  <text class="product-name product-name--first" x="566" y="450" text-anchor="middle">MINT</text>
  <path class="connector-swash" d="M652 392 Q690 380 732 386"/>
  <text class="connector" x="692" y="432" text-anchor="middle">and</text>
  <path class="connector-swash" d="M648 448 Q690 452 735 436"/>

  <text class="product-name product-name--second" x="622" y="530" text-anchor="middle">ROSEMARY</text>

  <text class="ingredients-note" x="621" y="620" text-anchor="middle">PLEASE ASK IN STORE TO SEE SPEC SHEET FOR INGREDIENTS</text>
</svg>
</body>
</html>
```